Marlow Vale Stud website

We would like to create a horse stud/agistment farm website similar to this websites we have attached below:
www.thornbeck.com.au
www.quillstead.com.au
www.brackley.com
www.pimsey.com.au
The main colour scheme are purple and white to align with the stable's racing colours.
We have also attach the company logo and also images of the farm and create some ideas for the website.
Many thanks for looking into this project!

```html
<!DOCTYPE html>
<html lang="en">
<head>
<meta charset="utf-8">
<title>Marlow Vale Stud</title>
<link href="https://fonts.googleapis.com/css2?family=Open+Sans:ital,wght@0,400;0,600;0,700;1,400&family=Montserrat:wght@600;700&display=swap" rel="stylesheet">
<style>
:root{
  --purple:#4b1f52;
  --purple-dark:#3a1640;
  --ink:#333;
  --muted:#777;
  --grey-band:#f1f1f1;
  --white:#fff;
}
*{box-sizing:border-box;margin:0;padding:0}
html,body{width:1200px;height:3140px;overflow:hidden}
body{font-family:"Open Sans",Arial,sans-serif;color:var(--ink);background:var(--white);position:relative}
a{color:inherit;text-decoration:none}

/* header */
.site-header{position:absolute;left:0;top:0;width:1200px;height:140px;background:var(--white)}
.brand{position:absolute;left:170px;top:26px;display:flex;align-items:center;gap:14px}
.brand-dot{width:56px;height:56px;border-radius:50%;background:var(--purple);display:block;flex:none}
.brand-name{font-weight:700;font-size:30px;color:var(--purple)}
.contact-bar{position:absolute;right:150px;top:40px;display:flex;gap:40px;font-size:17px;font-weight:600;color:#444}
.contact-bar span{display:flex;align-items:center;gap:10px}
.main-nav{position:absolute;left:240px;top:112px;display:flex;font-size:14px;font-weight:600}
.main-nav a{padding:4px 14px;color:#444}
.main-nav a.active{color:var(--purple);border-bottom:3px solid var(--purple)}
.nav-search{position:absolute;right:170px;top:108px;width:140px;height:30px;background:#555;color:#fff;font-size:13px;display:flex;align-items:center;justify-content:space-between;padding:0 10px}

/* hero */
.hero{position:absolute;left:0;top:140px;width:1200px;height:580px;background:linear-gradient(180deg,#6f7a55 0%,#4f5a3a 40%,#7a8b4a 75%,#2f3a1e 100%)}
.tweet-tab{position:absolute;left:690px;top:272px;height:28px;background:var(--purple-dark);color:#fff;font-size:13px;padding:0 14px;display:flex;gap:8px;align-items:center;z-index:2;white-space:nowrap}
.tweet-box{position:absolute;left:680px;top:300px;width:290px;height:210px;background:var(--purple);color:#fff;padding:40px 18px 18px;font-size:16px;line-height:1.35}
.hero-down{position:absolute;left:584px;top:682px;width:32px;height:38px;background:#fff;border-radius:16px 16px 0 0}

/* features */
.feature-row{position:absolute;left:20px;top:758px;width:1160px;display:flex;justify-content:space-between}
.feature{width:272px;height:200px;position:relative}
.feature-img{width:100%;height:100%}
.feature-cap{position:absolute;left:0;bottom:0;width:100%;height:34px;background:rgba(58,22,64,.85);color:#fff;font-size:14px;text-align:center;line-height:34px}

/* about */
.about-art{position:absolute;left:165px;top:1010px;width:250px;height:380px;border-radius:125px;background:radial-gradient(circle at 50% 45%,#b7c6d4,#6b7f8e 60%,#4f6a3a)}
.section-title{font-family:"Montserrat",sans-serif;font-weight:700;font-size:30px;color:#333}
.about{position:absolute;left:570px;top:1050px;width:520px}
.about p.lead{font-size:14px;color:var(--muted);line-height:1.5;margin:16px 0 18px}
.about-item{display:flex;gap:12px;margin-bottom:16px}
.about-item .tick{flex:none;width:18px;height:18px;border-radius:50%;border:2px solid var(--purple);margin-top:2px}
.about-item h4{font-size:15px;font-weight:600;color:#444}
.about-item p{font-size:12px;color:var(--muted);line-height:1.45}

/* testimonials */
.testimonials{position:absolute;left:0;top:1490px;width:1200px;height:380px;background:var(--grey-band);text-align:center}
.testimonials .section-title{margin-top:72px}
.quote{width:760px;margin:28px auto 0;font-size:27px;line-height:1.45;color:var(--purple);position:relative}
.quote-mark{position:absolute;font-size:70px;color:var(--purple);font-family:Georgia,serif;line-height:1}
.quote-author{margin-top:22px;font-size:22px;color:var(--purple);letter-spacing:1px}
.dots{display:flex;gap:12px;justify-content:center;margin-top:28px}
.dots i{width:16px;height:16px;border-radius:50%;border:2px solid #888;display:block}
.dots i.on{background:#888}

/* news */
.news{position:absolute;left:0;top:1960px;width:1200px;text-align:center}
.news-sub{font-size:13px;color:var(--muted);margin-top:10px}
.news-row{position:absolute;left:185px;top:100px;width:830px;display:flex;justify-content:space-between;text-align:left}
.news-card{width:262px;height:350px;background:#fff;box-shadow:0 1px 6px rgba(0,0,0,.15);position:relative}
.news-img{width:100%;height:166px}
.news-date{position:absolute;left:16px;top:130px;width:52px;height:52px;background:var(--purple);color:#fff;text-align:center;font-size:20px;font-weight:700;line-height:30px}
.news-date small{display:block;font-size:10px;line-height:10px;font-weight:400}
.news-body{padding:28px 18px 0}
.news-body h5{font-size:14px;font-weight:700;color:#333;line-height:1.3}
.news-body p{font-size:12px;color:var(--muted);line-height:1.45;margin-top:8px}
.news-body a{display:block;margin-top:8px;font-size:13px;font-weight:700;color:var(--purple)}
.news-arrow{position:absolute;top:270px;font-size:26px;color:#999}

/* video band */
.discover{position:absolute;left:0;top:2490px;width:1200px;height:270px;background:linear-gradient(180deg,#7fa05a 0%,#5c4232 50%,#3b2a1e 100%)}
.play{position:absolute;left:568px;top:78px;width:64px;height:64px}
.discover h3{position:absolute;left:0;top:190px;width:100%;text-align:center;color:#fff;font-family:"Montserrat",sans-serif;font-size:30px;letter-spacing:4px;font-weight:600}

/* footer */
.site-footer{position:absolute;left:0;top:2760px;width:1200px;height:380px;background:var(--purple);color:#e8dcea}
.footer-brand{position:absolute;left:170px;top:90px;width:110px;display:flex;flex-direction:column;align-items:flex-start;gap:10px}
.footer-brand .brand-dot{background:#fff;width:44px;height:44px}
.footer-brand span.name{font-weight:700;font-size:16px;line-height:1.3;color:#fff}
.footer-cols{position:absolute;left:300px;top:30px;display:flex}
.footer-col{width:185px;font-size:12px;line-height:1.8}
.footer-col h6{font-size:14px;font-weight:700;color:#fff;margin-bottom:4px}
.footer-bottom{position:absolute;left:170px;top:280px;width:860px;border-top:1px solid rgba(255,255,255,.25);padding-top:18px;display:flex;justify-content:space-between;font-size:12px}
.cards{display:flex;gap:6px}
.cards i{width:40px;height:24px;background:#ddd;border-radius:3px;display:block}
</style>
</head>
<body>

<header class="site-header">
  <div class="brand"><span class="brand-dot"></span><span class="brand-name">Marlow Vale Stud</span></div>
  <div class="contact-bar">
    <span><svg width="16" height="16" viewBox="0 0 24 24"><path fill="#4b1f52" d="M6.6 10.8a15 15 0 0 0 6.6 6.6l2.2-2.2c.3-.3.7-.4 1-.2 1.1.4 2.3.6 3.6.6.6 0 1 .4 1 1V20c0 .6-.4 1-1 1A17 17 0 0 1 3 4c0-.6.4-1 1-1h3.5c.6 0 1 .4 1 1 0 1.3.2 2.5.6 3.6.1.3 0 .7-.2 1z"/></svg>+1 555 014 2290</span>
    <span><svg width="18" height="14" viewBox="0 0 24 18"><rect x="1" y="1" width="22" height="16" fill="none" stroke="#4b1f52" stroke-width="2"/><path d="M1 1l11 9 11-9" fill="none" stroke="#4b1f52" stroke-width="2"/></svg>info@marlowvale</span>
  </div>
  <nav class="main-nav">
    <a class="active">Home</a><a>About Us</a><a>Farm</a><a>Latest News</a><a>Testimonials</a><a>Our Team</a><a>Contact</a>
  </nav>
  <div class="nav-search">Search <svg width="14" height="14" viewBox="0 0 24 24"><circle cx="10" cy="10" r="7" fill="none" stroke="#fff" stroke-width="3"/><path d="M15 15l7 7" stroke="#fff" stroke-width="3"/></svg></div>
</header>

<section class="hero" role="img" aria-label="Jockey in white silks riding a racehorse over the track rail, crowd behind"></section>
<div class="tweet-tab"><svg width="12" height="12"><circle cx="6" cy="6" r="5" fill="#fff"/></svg>FollowMarlowValeStud</div>
<div class="tweet-box">@MarlowValeStud<br>@<br>At vero eos et accusamus et iusto odio dignissimos ducimus qui blanditiis praesentium voluptatum...</div>
<div class="hero-down"></div>

<section class="feature-row">
  <div class="feature"><div class="feature-img" role="img" aria-label="Black horse rearing in a field" style="background:linear-gradient(180deg,#8fb4d8,#5d7a4a)"></div><div class="feature-cap">Accusamus Dignissim</div></div>
  <div class="feature"><div class="feature-img" role="img" aria-label="Dark horse galloping across grass" style="background:linear-gradient(180deg,#c9d3dc,#7d8a6a)"></div><div class="feature-cap">Molestias Excepturi</div></div>
  <div class="feature"><div class="feature-img" role="img" aria-label="Brown horse standing in a paddock" style="background:linear-gradient(180deg,#9cc0df,#6f8f3e)"></div><div class="feature-cap">Provident Similique</div></div>
  <div class="feature"><div class="feature-img" role="img" aria-label="White horse rearing against a dark background" style="background:linear-gradient(180deg,#3b3f45,#6b6f74)"></div><div class="feature-cap">Voluptas Assumenda</div></div>
</section>

<div class="about-art" role="img" aria-label="Rounded panel filled with horse and farm imagery"></div>
<section class="about">
  <h2 class="section-title">ABOUT US</h2>
  <p class="lead">Lorem Ipsum is simply dummy text of the printing and typesetting industry. It has been the industry's standard dummy text ever since the 1500s, when an unknown printer took a galley of type.</p>
  <div class="about-item"><span class="tick"></span><div><h4>Sed ut perspiciatis unde</h4><p>At vero eos et accusamus et iusto odio dignissimos<br>ducimus qui blanditiis praesentium voluptatum</p></div></div>
  <div class="about-item"><span class="tick"></span><div><h4>Sed ut perspiciatis unde</h4><p>At vero eos et accusamus et iusto odio dignissimos<br>ducimus qui blanditiis praesentium voluptatum</p></div></div>
  <div class="about-item"><span class="tick"></span><div><h4>Sed ut perspiciatis unde</h4><p>At vero eos et accusamus et iusto odio dignissimos<br>ducimus qui blanditiis praesentium voluptatum</p></div></div>
</section>

<section class="testimonials">
  <h2 class="section-title">TESTIMONIALS</h2>
  <div class="quote"><span class="quote-mark" style="left:-60px;top:-8px">&ldquo;</span>At vero eos et accusamus et iusto odio dignissimos ducimus qui blanditiis praesentium voluptatum deleniti atque<span class="quote-mark" style="right:-60px;bottom:-40px">&rdquo;</span></div>
  <div class="quote-author">&ndash; JOHN DEO</div>
  <div class="dots"><i></i><i class="on"></i><i></i></div>
</section>

<section class="news">
  <h2 class="section-title">LATEST NEWS</h2>
  <p class="news-sub">Lorem Ipsum Dolor Sit Amet Consectetur</p>
  <span class="news-arrow" style="left:80px">&lsaquo;</span>
  <span class="news-arrow" style="right:80px">&rsaquo;</span>
  <div class="news-row">
    <article class="news-card"><div class="news-img" role="img" aria-label="Horse grazing in a green field" style="background:linear-gradient(180deg,#a9c6e0,#5f8a3a)"></div><div class="news-date">07<small>MAR</small></div><div class="news-body"><h5>Sed ut perspiciatis unde omnis iste natus</h5><p>Sed ut perspiciatis unde omnis iste natus error sit voluptatem accusantium dolore laudantium</p><a>Read More</a></div></article>
    <article class="news-card"><div class="news-img" role="img" aria-label="Trainer standing beside a bay horse" style="background:linear-gradient(180deg,#c4b8a4,#6b4a34)"></div><div class="news-date">07<small>MAR</small></div><div class="news-body"><h5>Sed ut perspiciatis unde omnis iste natus</h5><p>Sed ut perspiciatis unde omnis iste natus error sit voluptatem accusantium dolore laudantium</p><a>Read More</a></div></article>
    <article class="news-card"><div class="news-img" role="img" aria-label="Group of people at a horse sale" style="background:linear-gradient(180deg,#b9c2cc,#5a6470)"></div><div class="news-date">07<small>MAR</small></div><div class="news-body"><h5>Sed ut perspiciatis unde omnis iste natus</h5><p>Sed ut perspiciatis unde omnis iste natus error sit voluptatem accusantium dolore laudantium</p><a>Read More</a></div></article>
  </div>
</section>

<section class="discover" role="img" aria-label="Two bay horses looking over a wooden paddock fence">
  <svg class="play" viewBox="0 0 64 64"><circle cx="32" cy="32" r="32" fill="#fff"/><path d="M26 20l18 12-18 12z" fill="#c0392b"/></svg>
  <h3>DISCOVER GREATNESS</h3>
</section>

<footer class="site-footer">
  <div class="footer-brand"><span class="brand-dot"></span><span class="name">Marlow Vale Stud</span></div>
  <div class="footer-cols">
    <div class="footer-col"><h6>Quick Links</h6>&rsaquo; Home<br>&rsaquo; About Us<br>&rsaquo; Testimonials<br>&rsaquo; Contact Us</div>
    <div class="footer-col"><h6>Information</h6>&rsaquo; About Farm<br>&rsaquo; Nominations<br>&rsaquo; Stallions<br>&rsaquo; Terms &amp; Conditions<br>&rsaquo; Our Sitemap</div>
    <div class="footer-col"><h6>My Account</h6>&rsaquo; Gallery Profile<br>&rsaquo; Community Profile<br>&rsaquo; Updates Profile<br>&rsaquo; Latest News<br>&rsaquo; Our Blog</div>
    <div class="footer-col"><h6>Address</h6>14 Harrow Lane, Hill Valley<br>Lorem Ipsum<br>&#9742; +1 555 014 2290<br>&#9993; info@marlowvalestud.com</div>
  </div>
  <div class="footer-bottom"><span>Copyright &copy; 2024 . All Rights Reserved</span><span class="cards"><i></i><i></i><i></i><i></i></span></div>
</footer>

</body>
</html>
```